Business Card Design for Marketing Firm

Looking for business card design for higher end marketing firm. Clean but impressionable/trendy. We are a marketing firm that represents manufacturers in the foodservice equipment and supply industry. Our customers are end users such has hotels, restaurants, country clubs, convention centers and casinos as well as distributors of restaurants supplies and equipment, and manufacturers of foodservice equipment and supplies.
Target Market(s)
Hotels, Restaurants, Supply & Equipment Distributors, Foodservice Manufacturers
Industry/Entity Type
Foodservice/Hospitality
Contact Information for Business Card
Name, Title, Contact Number, Email, Website, Social Media, Address
Requirements
Must have
- Clean & Simple but Serious and Impressionable

```html
<!DOCTYPE html>
<html lang="en">
<head>
<meta charset="utf-8">
<title>Meridian Service Partners — Business Card</title>
<link href="https://fonts.googleapis.com/css2?family=Cinzel:wght@500&family=Poppins:wght@400;600&display=swap" rel="stylesheet">
<style>
  :root {
    --brand-blue: #0a0a8e;
    --paper: #ffffff;
    --backdrop: #2a2a2a;
  }
  * { box-sizing: border-box; margin: 0; padding: 0; }
  html, body { width: 1200px; height: 1015px; overflow: hidden; }
  body {
    background: var(--backdrop);
    font-family: "Poppins", sans-serif;
    position: relative;
  }
  .card {
    position: absolute;
    left: 200px;
    width: 800px;
    height: 457px;
    overflow: hidden;
  }
  .card--back { top: 30px; background: var(--brand-blue); }
  .card--front { top: 527px; background: var(--brand-blue); }

  .wordmark {
    font-family: "Cinzel", serif;
    font-weight: 500;
    letter-spacing: 2px;
    line-height: 1.15;
    text-align: center;
  }
  .card--back .brand {
    position: absolute;
    left: 0; right: 0; top: 150px;
    display: flex; flex-direction: column; align-items: center;
    color: var(--paper);
  }
  .card--back .wordmark { font-size: 40px; }
  .brand-rule {
    width: 420px; height: 2px; background: currentColor; margin-top: 14px;
  }
  .social-row { display: flex; gap: 10px; margin-top: 22px; }
  .social-dot {
    width: 34px; height: 34px; border-radius: 50%;
    border: 2px solid var(--paper);
  }

  .front-shape { position: absolute; inset: 0; }
  .card--front .brand {
    position: absolute;
    left: 470px; top: 130px; width: 270px;
    display: flex; flex-direction: column; align-items: center;
    color: var(--brand-blue);
  }
  .card--front .wordmark { font-size: 26px; }
  .card--front .brand-rule { width: 250px; height: 1.5px; margin-top: 10px; }

  .person { position: absolute; left: 70px; top: 120px; color: var(--paper); }
  .person-name { font-weight: 600; font-size: 30px; letter-spacing: 1px; text-transform: uppercase; }
  .person-title { font-size: 18px; margin-top: -2px; }

  .address {
    position: absolute; left: 70px; top: 255px;
    color: var(--paper); font-size: 18px; line-height: 1.3;
  }
  .contact-list {
    position: absolute; left: 70px; top: 325px;
    list-style: none; color: var(--paper); font-size: 18px; line-height: 1.45;
  }
  .contact-list li { display: flex; align-items: center; gap: 10px; }
  .contact-icon { width: 18px; height: 18px; flex: none; }
</style>
</head>
<body>

<section class="card card--back" aria-label="Card back">
  <div class="brand">
    <p class="wordmark">Meridian Service<br>Partners</p>
    <span class="brand-rule"></span>
    <div class="social-row" aria-label="Social media">
      <span class="social-dot"></span>
      <span class="social-dot"></span>
      <span class="social-dot"></span>
    </div>
  </div>
</section>

<section class="card card--front" aria-label="Card front">
  <svg class="front-shape" viewBox="0 0 800 457" width="800" height="457" aria-hidden="true">
    <circle cx="585" cy="178" r="290" fill="none" stroke="#ffffff" stroke-width="6"/>
    <circle cx="605" cy="168" r="272" fill="#ffffff"/>
  </svg>

  <div class="brand">
    <p class="wordmark">Meridian Service<br>Partners</p>
    <span class="brand-rule"></span>
  </div>

  <div class="person">
    <h1 class="person-name">Marcus Reed</h1>
    <p class="person-title">Managing Director</p>
  </div>

  <p class="address">128, Street line here<br>City Name, 10234</p>

  <ul class="contact-list">
    <li>
      <svg class="contact-icon" viewBox="0 0 24 24" fill="#fff"><path d="M6.6 10.8a15.1 15.1 0 0 0 6.6 6.6l2.2-2.2a1 1 0 0 1 1-.25 11.4 11.4 0 0 0 3.6.57 1 1 0 0 1 1 1V20a1 1 0 0 1-1 1A17 17 0 0 1 3 4a1 1 0 0 1 1-1h3.5a1 1 0 0 1 1 1c0 1.25.2 2.45.57 3.57a1 1 0 0 1-.25 1z"/></svg>
      044-321 654 987
    </li>
    <li>
      <svg class="contact-icon" viewBox="0 0 24 24" fill="none" stroke="#fff" stroke-width="2"><rect x="2" y="5" width="20" height="14" rx="1"/><path d="M2 6l10 7 10-7"/></svg>
      info@yourdomain.com
    </li>
    <li>
      <svg class="contact-icon" viewBox="0 0 24 24" fill="none" stroke="#fff" stroke-width="1.8"><circle cx="12" cy="12" r="10"/><path d="M2 12h20M12 2c3 3 3 17 0 20M12 2c-3 3-3 17 0 20"/></svg>
      www.yourdomain.com
    </li>
  </ul>
</section>

</body>
</html>
```